Harborline Renewal Business Card Design

Professional and clean design. The design colors should flow with the logo. Two-sided card with the website on the back which is:

www.HarborlineRenewal.example.

"Specializing in Water Damage Restoration"

On the front I need the name, email, phone, and logo.

Name: Darnell Quisby
Email: Darnell@HarborlineRenewal.example
Phone: 555-318-2046 for now

I only have the Preview and Thumbnail right now but should have the source files uploaded within a day or two.

Target Market(s)

Flood victims, home owners with water damage from busted pipes etc...

Industry/Entity Type

Business

Contact Information for Business Card

Name: Darnell Quisby

Font styles to use
Serif
Sans Serif

Requirements
Must have
• Business Card Details Info

```html
<!DOCTYPE html>
<html lang="en">
<head>
<meta charset="utf-8">
<title>Harborline Renewal Business Card</title>
<link rel="stylesheet" href="https://fonts.googleapis.com/css2?family=Cinzel:wght@500&family=Source+Sans+3:wght@400;700&display=swap">
<style>
  :root {
    --page-bg: #d8d3cc;
    --card-bg: #eef2f4;
    --brand-blue: #2f80b3;
    --name-teal: #2d7497;
    --deep-blue: #145f96;
    --mid-blue: #2a86c4;
    --light-blue: #5fb4e4;
    --icon-bg: #3c86ad;
  }
  * { margin: 0; padding: 0; box-sizing: border-box; }
  html, body {
    width: 1200px; height: 970px; overflow: hidden;
    background: var(--page-bg);
  }
  .card {
    position: absolute; left: 100px; top: 200px;
    width: 1000px; height: 569px;
    background: var(--card-bg);
    box-shadow: 0 10px 30px rgba(0,0,0,0.18);
    overflow: hidden;
  }
  .card-swoosh { position: absolute; inset: 0; width: 1000px; height: 569px; }
  .brand-mark {
    position: absolute; left: 205px; top: 45px;
    width: 128px; height: 128px; border-radius: 50%;
    background: var(--brand-blue);
  }
  .brand-name {
    position: absolute; left: 43px; top: 196px; width: 460px;
    text-align: center;
    font-family: "Cinzel", Georgia, serif; font-weight: 500;
    color: var(--brand-blue); line-height: 1;
  }
  .brand-name .line-one { display: block; font-size: 54px; letter-spacing: 1px; }
  .brand-name .line-two { display: block; font-size: 26px; letter-spacing: 8px; margin-top: 8px; }
  .tagline {
    position: absolute; left: 50px; top: 286px; width: 440px; text-align: center;
    font-family: "Source Sans 3", Arial, sans-serif; font-size: 21px;
    color: var(--brand-blue);
  }
  .person-name {
    position: absolute; left: 50px; top: 342px;
    font-family: "Source Sans 3", Arial, sans-serif; font-weight: 700; font-size: 37px;
    color: var(--name-teal);
  }
  .contact-list { position: absolute; left: 50px; top: 414px; list-style: none; }
  .contact-list li {
    display: flex; align-items: center; gap: 8px; height: 36px;
    font-family: "Source Sans 3", Arial, sans-serif; font-size: 27px;
    color: var(--brand-blue);
  }
  .contact-icon {
    width: 26px; height: 26px; background: var(--icon-bg); border-radius: 3px;
    display: flex; align-items: center; justify-content: center; flex-shrink: 0;
  }
</style>
</head>
<body>
  <div class="card">
    <svg class="card-swoosh" viewBox="0 0 1000 569" aria-hidden="true">
      <defs>
        <linearGradient id="bandFill" x1="0" y1="0" x2="1" y2="1">
          <stop offset="0" stop-color="#2f8ccb"/>
          <stop offset="0.55" stop-color="#1c6fa8"/>
          <stop offset="1" stop-color="#114f84"/>
        </linearGradient>
        <linearGradient id="arcStroke" x1="0" y1="0" x2="0" y2="1">
          <stop offset="0" stop-color="#1c6b9c"/>
          <stop offset="0.5" stop-color="#3aa0dc"/>
          <stop offset="1" stop-color="#1c6b9c"/>
        </linearGradient>
      </defs>
      <path d="M620 0 C800 40 930 170 895 310 C870 420 800 510 725 569 L1000 569 L1000 0 Z" fill="url(#bandFill)"/>
      <path d="M630 4 C800 50 915 175 880 310 C855 415 790 505 718 569" fill="none" stroke="#5fb4e4" stroke-width="10" opacity="0.8"/>
      <path d="M370 0 C620 40 900 170 880 340 C870 430 800 510 720 569" fill="none" stroke="url(#arcStroke)" stroke-width="7"/>
    </svg>

    <div class="brand-mark"></div>
    <div class="brand-name">
      <span class="line-one">HARBORLINE</span>
      <span class="line-two">RENEWAL</span>
    </div>
    <p class="tagline">Specializing in Water Damage Restoration</p>

    <h1 class="person-name">Darnell Quisby</h1>
    <ul class="contact-list">
      <li>
        <span class="contact-icon">
          <svg width="18" height="18" viewBox="0 0 24 24" aria-hidden="true"><path d="M6.6 10.8a15.5 15.5 0 0 0 6.6 6.6l2.2-2.2a1 1 0 0 1 1-.25 11.4 11.4 0 0 0 3.6.6 1 1 0 0 1 1 1V20a1 1 0 0 1-1 1A17 17 0 0 1 3 4a1 1 0 0 1 1-1h3.5a1 1 0 0 1 1 1c0 1.25.2 2.45.6 3.6a1 1 0 0 1-.25 1z" fill="#fff"/></svg>
        </span>555-318-2046
      </li>
      <li>
        <span class="contact-icon">
          <svg width="18" height="14" viewBox="0 0 24 18" aria-hidden="true"><rect x="1" y="1" width="22" height="16" fill="none" stroke="#fff" stroke-width="2"/><path d="M1 1 L12 10 L23 1 M1 17 L9 8 M23 17 L15 8" fill="none" stroke="#fff" stroke-width="2"/></svg>
        </span>Darnell@HarborlineRenewal.example
      </li>
      <li>
        <span class="contact-icon">
          <svg width="18" height="18" viewBox="0 0 24 24" aria-hidden="true"><circle cx="12" cy="12" r="10" fill="none" stroke="#fff" stroke-width="2"/><ellipse cx="12" cy="12" rx="4.5" ry="10" fill="none" stroke="#fff" stroke-width="1.6"/><path d="M2 12h20M4 7h16M4 17h16" stroke="#fff" stroke-width="1.6"/></svg>
        </span>www.HarborlineRenewal.example
      </li>
    </ul>
  </div>
</body>
</html>
```